Membership Based Medical Practice Website

We need a functioning website for a new Membership based medical practice. There will be an enrollment fee and a monthly fee. We would like to see designs that are modern, simple. Should use neutral light colors. Examples of sites we like are www.kellanmoorclinic.com and https://fernholtcare.com/ We also have a link that when "Join Now" is clicked it will go to the signup website.

Target Market(s)

Gay Men, local population, Age group 20 to 60's.

Industry/Entity Type

Medical

Coding

Coded - Design and coding required

Number of Pages Required

5+ page

Font styles to use
Sans Serif

Colors
ffffff
cee9f5
ecf7fb
cfeae6
edf8f6
aaaaaa
e9e9e9
dbdbdb
fff3d1

Requirements
Must have
• Logo and header on every page. Clean, simple design, clear content, mobile compatible.
• Must use Wordpress
Nice to have
• Ideas should come from kellanmoorclinic.com
• Easy to read
Should not have
• Generic patient pictures, bold colors.
• Should not copy from above websites.

```html
<!DOCTYPE html>
<html lang="en">
<head>
<meta charset="utf-8">
<title>Larkmont Infectious Disease Specialists</title>
<link href="https://fonts.googleapis.com/css2?family=Open+Sans:wght@300;400;600;700&display=swap" rel="stylesheet">
<style>
:root{
  --white:#ffffff;
  --sky:#cee9f5;
  --sky-light:#ecf7fb;
  --grey-band:#e9e9e9;
  --grey-footer:#dbdbdb;
  --grey-text:#aaaaaa;
  --cream:#fff3d1;
  --gold:#d9a441;
  --ink:#333333;
  --ink-soft:#555555;
}
*{margin:0;padding:0;box-sizing:border-box}
html,body{width:1200px;height:2961px;overflow:hidden}
body{font-family:"Open Sans",sans-serif;color:var(--ink);background:var(--white);position:relative}
.abs{position:absolute}

/* header */
.site-header{position:absolute;left:0;top:0;width:1200px;height:112px;background:var(--white)}
.brand{position:absolute;left:118px;top:22px;width:200px;text-align:center;color:var(--gold)}
.brand-dot{width:40px;height:40px;border-radius:50%;border:2px solid var(--gold);margin:0 auto 6px}
.brand-name{font-size:13px;letter-spacing:7px;line-height:1.2}
.brand-sub{font-size:10px;letter-spacing:.5px}
.main-nav{position:absolute;left:0;top:0;width:1200px;height:112px;font-size:12px;color:var(--ink)}
.main-nav span{position:absolute;top:51px;white-space:nowrap}
.btn-join{position:absolute;left:965px;top:41px;width:92px;height:38px;border:2px solid var(--ink);font-size:12px;display:flex;align-items:center;justify-content:center}

/* hero */
.hero{position:absolute;left:0;top:112px;width:1200px;height:480px;
  background:linear-gradient(180deg,#b89a86 0%,#8d6d5b 45%,#6e5446 100%)}
.hero h1{position:absolute;left:0;width:1200px;top:244px;text-align:center;color:var(--white);font-weight:700;font-size:25px;letter-spacing:.3px;text-transform:uppercase}

/* specialties */
.specialties{position:absolute;left:0;top:592px;width:1200px;height:676px;background:var(--grey-band)}
.section-title{position:absolute;left:0;width:1200px;text-align:center;font-weight:300;font-size:27px;color:var(--ink)}
.section-sub{position:absolute;left:0;width:1200px;text-align:center;font-weight:300;font-size:18px}
.spec-icon{position:absolute;width:36px;height:36px;border-radius:50%;background:var(--white)}
.spec-label{position:absolute;font-size:12px;color:var(--ink);white-space:nowrap}
.spec-label.left{text-align:right;width:300px}

/* benefits */
.benefits{position:absolute;left:0;top:1268px;width:1200px;height:787px;background:var(--white)}
.benefit{position:absolute;width:200px;text-align:center}
.benefit-icon{width:138px;height:138px;border-radius:50%;background:var(--sky-light);border:5px solid var(--sky);margin:0 auto;display:flex;align-items:center;justify-content:center}
.benefit h3{font-weight:400;font-size:15px;margin-top:18px}
.benefit p{font-size:11px;line-height:18px;color:var(--ink-soft);margin-top:10px;padding:0 6px}

/* pricing */
.pricing{position:absolute;left:0;top:2055px;width:1200px;height:527px;
  background:linear-gradient(180deg,#ffffff 0%,#f4f4f3 45%,#e4e6e6 100%)}
.price-list{position:absolute;left:345px;top:182px;list-style:none;font-size:14px;color:var(--ink-soft)}
.price-list li{height:35px;display:flex;align-items:center;gap:10px}
.btn-outline{position:absolute;left:480px;top:405px;width:242px;height:53px;border:2px solid var(--ink);display:flex;align-items:center;justify-content:center;font-size:15px;background:transparent}

/* footer */
.site-footer{position:absolute;left:0;top:2582px;width:1200px;height:379px;background:var(--grey-footer)}
.footer-brand{position:absolute;left:140px;top:75px;width:210px;text-align:center;color:var(--ink-soft)}
.footer-brand .brand-dot{width:60px;height:60px;border-color:var(--gold)}
.footer-brand .brand-name{font-size:15px;letter-spacing:9px;margin-top:10px}
.footer-brand .brand-sub{font-size:12px}
.footer-col h4{font-weight:400;font-size:18px;color:var(--ink-soft)}
.footer-links{list-style:none;margin-top:22px;font-size:12px;color:var(--ink-soft)}
.footer-links li{height:31px}
.contact-row{display:flex;gap:12px;font-size:12px;color:var(--ink-soft);line-height:17px;margin-top:22px}
.social{position:absolute;width:38px;height:38px;border-radius:50%;background:#aaaaaa}
.footer-rule{position:absolute;left:145px;top:314px;width:910px;height:1px;background:#c6c6c6}
.copyright{position:absolute;left:0;width:1200px;top:336px;text-align:center;font-size:11px;color:var(--ink-soft)}
</style>
</head>
<body>

<header class="site-header">
  <div class="brand">
    <div class="brand-dot"></div>
    <div class="brand-name">LARKMONT</div>
    <div class="brand-sub">INFECTIOUS DISEASE SPECIALISTS</div>
  </div>
  <nav class="main-nav">
    <span style="left:466px">HOME</span>
    <span style="left:545px">SPECIALTIES</span>
    <span style="left:655px">PRICING</span>
    <span style="left:742px">ABOUT US</span>
    <span style="left:847px">FAQ</span>
    <span style="left:912px">BLOG</span>
  </nav>
  <div class="btn-join">JOIN US</div>
</header>

<section class="hero" role="img" aria-label="Photo of two runners' legs on a sandy beach at sunset">
  <h1>Specialty medicine with commitment, compassion and care</h1>
</section>

<section class="specialties">
  <h2 class="section-title" style="top:74px">We offer comprehensive treatment of a wide variety of infectious diseases.</h2>
  <p class="section-sub" style="top:114px">Out expertise is in the following area.</p>

  <svg class="abs" style="left:0;top:0" width="1200" height="676">
    <g stroke="#d6d6d6" stroke-width="1" fill="none">
      <line x1="431" y1="228" x2="540" y2="228"/>
      <line x1="431" y1="293" x2="505" y2="293"/>
      <line x1="431" y1="358" x2="490" y2="358"/>
      <line x1="431" y1="421" x2="505" y2="421"/>
      <line x1="660" y1="246" x2="772" y2="246"/>
      <line x1="697" y1="310" x2="772" y2="310"/>
      <line x1="710" y1="374" x2="772" y2="374"/>
      <line x1="697" y1="438" x2="772" y2="438"/>
      <line x1="600" y1="453" x2="600" y2="515"/>
    </g>
    <circle cx="600" cy="338" r="115" fill="#ffffff"/>
    <circle cx="600" cy="338" r="97" fill="#fff3d1"/>
    <circle cx="600" cy="338" r="22" fill="none" stroke="#d9a441" stroke-width="1.5"/>
  </svg>

  <div class="spec-icon" style="left:395px;top:210px"></div>
  <div class="spec-icon" style="left:395px;top:275px"></div>
  <div class="spec-icon" style="left:395px;top:340px"></div>
  <div class="spec-icon" style="left:395px;top:403px"></div>
  <div class="spec-icon" style="left:772px;top:228px"></div>
  <div class="spec-icon" style="left:772px;top:292px"></div>
  <div class="spec-icon" style="left:772px;top:356px"></div>
  <div class="spec-icon" style="left:772px;top:420px"></div>
  <div class="spec-icon" style="left:582px;top:515px"></div>

  <div class="spec-label left" style="left:87px;top:220px">HIV/PrEP</div>
  <div class="spec-label left" style="left:87px;top:285px">Chronic Hepatitis</div>
  <div class="spec-label left" style="left:87px;top:350px">Sexually transmitted infections</div>
  <div class="spec-label left" style="left:87px;top:413px">Pre-travel vaccinations and counselling</div>
  <div class="spec-label" style="left:821px;top:238px">Infections associated with medical devices</div>
  <div class="spec-label" style="left:821px;top:302px">Bone and Joint infections</div>
  <div class="spec-label" style="left:821px;top:366px">Postsurgical infections</div>
  <div class="spec-label" style="left:821px;top:430px">Diabetes related infections</div>
  <div class="spec-label" style="left:565px;top:557px">Tuberculosis</div>
</section>

<section class="benefits">
  <h2 class="section-title" style="top:85px;font-size:34px">Less wait, more personal.</h2>
  <p class="section-sub" style="top:134px;color:var(--grey-text);font-size:17px">We are not your traditional doctor's office.</p>

  <div class="benefit" style="left:140px;top:200px">
    <div class="benefit-icon"><svg width="60" height="60" fill="none" stroke="#666" stroke-width="2"><path d="M12 30 L30 12 H48 V30 L30 48 Z"/><circle cx="40" cy="20" r="3"/></svg></div>
    <h3>Straightforward pricing</h3>
    <p>We charge all our patients the same low rate - no surprises.</p>
  </div>
  <div class="benefit" style="left:380px;top:200px">
    <div class="benefit-icon"><svg width="60" height="60" fill="none" stroke="#666" stroke-width="2"><rect x="14" y="10" width="32" height="40" rx="3"/><line x1="22" y1="22" x2="38" y2="22"/><line x1="22" y1="30" x2="38" y2="30"/><line x1="22" y1="38" x2="32" y2="38"/></svg></div>
    <h3>Available when you are</h3>
    <p>New patient appointments are available within 1 week.</p>
  </div>
  <div class="benefit" style="left:620px;top:200px">
    <div class="benefit-icon"><svg width="60" height="60" fill="none" stroke="#666" stroke-width="2"><rect x="8" y="12" width="34" height="36" rx="2"/><line x1="8" y1="20" x2="42" y2="20"/><circle cx="42" cy="40" r="12" fill="#ecf7fb"/><path d="M42 33 V40 H48"/></svg></div>
    <h3>Hassle-free booking</h3>
    <p>Schedule your appointment online at your convenience - no need to call during business hours.</p>
  </div>
  <div class="benefit" style="left:860px;top:200px">
    <div class="benefit-icon"><svg width="60" height="60" fill="none" stroke="#666" stroke-width="2"><path d="M30 46 L14 30 A8 8 0 0 1 30 18 A8 8 0 0 1 46 30 Z"/></svg></div>
    <h3>Devoted care</h3>
    <p>We schedule enough time at each visit to make sure all of your questions are answered.</p>
  </div>

  <div class="benefit" style="left:140px;top:480px">
    <div class="benefit-icon"><svg width="60" height="60" fill="none" stroke="#666" stroke-width="2"><path d="M8 26 L20 18 L30 24 L40 18 L52 26 L38 40 L22 40 Z"/></svg></div>
    <h3>Within your reach</h3>
    <p>Follow-up appointments may be done by video chat for your convenience.</p>
  </div>
  <div class="benefit" style="left:380px;top:480px">
    <div class="benefit-icon"><svg width="60" height="60" fill="none" stroke="#666" stroke-width="2"><path d="M12 12 H42 L48 18 V48 H12 Z"/><rect x="20" y="12" width="18" height="12"/><line x1="20" y1="34" x2="40" y2="34"/><line x1="20" y1="40" x2="40" y2="40"/></svg></div>
    <h3>Save on lab costs</h3>
    <p>If paying upfront for labs, we offer discounted pricing of up to 90% off standard rates.</p>
  </div>
  <div class="benefit" style="left:620px;top:480px">
    <div class="benefit-icon"><svg width="60" height="60" fill="none" stroke="#666" stroke-width="2"><rect x="8" y="20" width="44" height="20" rx="10" transform="rotate(-40 30 30)"/><line x1="24" y1="22" x2="36" y2="38"/></svg></div>
    <h3>Save on medications</h3>
    <p>We offer deeply discounted wholesale price medications for our members at pharmacy on site.</p>
  </div>
  <div class="benefit" style="left:860px;top:480px">
    <div class="benefit-icon"><svg width="60" height="60" fill="none" stroke="#666" stroke-width="2"><circle cx="30" cy="30" r="20"/><line x1="16" y1="44" x2="44" y2="16"/></svg></div>
    <h3>No middle man</h3>
    <p>We don't bill any insurance plans so decisions about your healthcare will be made by you and Dr. Halvorsen, without the impersonal management that comes from third-party payers.</p>
  </div>
</section>

<section class="pricing" role="img" aria-label="Faint photo of an open road stretching toward hills under a pale sky">
  <h2 class="section-title" style="top:78px;font-size:34px">Our pricing is simple, transparent and affordable.</h2>
  <p class="section-sub" style="top:124px;color:var(--grey-text);font-size:22px">Membership Plan $80/mo, plus a one-time $99 enrollment fee.</p>
  <ul class="price-list">
    <li><svg width="13" height="11"><path d="M1 6 L5 10 L12 1" fill="none" stroke="#777" stroke-width="2"/></svg>Includes all appointments, no co-pay</li>
    <li><svg width="13" height="11"><path d="M1 6 L5 10 L12 1" fill="none" stroke="#777" stroke-width="2"/></svg>Relaxed, unrushed visits</li>
    <li><svg width="13" height="11"><path d="M1 6 L5 10 L12 1" fill="none" stroke="#777" stroke-width="2"/></svg>Direct communication with your doctor via phone, email, video chat 24/7</li>
    <li><svg width="13" height="11"><path d="M1 6 L5 10 L12 1" fill="none" stroke="#777" stroke-width="2"/></svg>Convenient online scheduling (no need to call during business hours)</li>
    <li><svg width="13" height="11"><path d="M1 6 L5 10 L12 1" fill="none" stroke="#777" stroke-width="2"/></svg>Wholesale price for labs and medications</li>
  </ul>
  <div class="btn-outline">LEARN MORE ABOUT US</div>
</section>

<footer class="site-footer">
  <div class="footer-brand">
    <div class="brand-dot"></div>
    <div class="brand-name">LARKMONT</div>
    <div class="brand-sub">INFECTIOUS DISEASE SPECIALISTS</div>
  </div>

  <div class="footer-col abs" style="left:440px;top:72px">
    <h4>Links</h4>
    <ul class="footer-links">
      <li>Home</li><li>Specialties</li><li>Pricing</li><li>About Us</li><li>FAQ</li><li>Blog</li>
    </ul>
  </div>

  <div class="footer-col abs" style="left:625px;top:72px;width:200px">
    <h4>Contact</h4>
    <div class="contact-row"><svg width="10" height="14"><path d="M5 13 C1 8 1 6 1 5 A4 4 0 0 1 9 5 C9 6 9 8 5 13 Z" fill="#999"/></svg><div>Larkmont<br>Infectious Disease Specialists<br>City name.</div></div>
    <div class="contact-row" style="margin-top:28px"><svg width="12" height="12"><path d="M2 1 L5 1 L6 4 L4 5 A7 7 0 0 0 7 8 L8 6 L11 7 L11 10 A1 1 0 0 1 10 11 A9 9 0 0 1 1 2 A1 1 0 0 1 2 1 Z" fill="#999"/></svg>555-014-2290</div>
    <div class="contact-row" style="margin-top:22px"><svg width="13" height="10"><rect x="0.5" y="0.5" width="12" height="9" fill="#999"/><path d="M0.5 0.5 L6.5 5 L12.5 0.5" fill="none" stroke="#dbdbdb"/></svg>hello@larkmontid.com</div>
  </div>

  <div class="footer-col abs" style="left:916px;top:72px"><h4>Get Connected</h4></div>
  <div class="social" style="left:916px;top:128px"></div>
  <div class="social" style="left:963px;top:128px"></div>
  <div class="social" style="left:1009px;top:128px"></div>

  <div class="footer-rule"></div>
  <p class="copyright">Copyrights © 2019 LARKMONT INFECTIOUS DISEASE SPECIALISTS. All rights reserved.</p>
</footer>

</body>
</html>
```